Luxury Wine Label for New Startup Winery

We need a wine label for our new winery startup. We have worked with a local designer but do not feel the resulting label / logo have the elevation required to present our brand as a luxury wine. Our winery is called "Quailbrook Vineyards" and we are focused on extremely high quality hand crafted artisan and estate wines from the Pacific Northwest.
We would like to see designs that utilize a tree line, or other imagery that represents the "Quailbrook" part of our company name. Another interesting feature could be wood grain.
A logo will be required based on your design so please design with this in mind:
This logo should be consistent with the wine bottle label design, and should be representative of our high end exclusive wine while giving a sense of place (Oregon/ Pacific Northwest.)
I will supply an image of the design we received from our local designer, PLEASE NOTE: in general we do like wood grain and tree line concepts but feel the execution was poorly done.
ATTN: Logo design should be suitable for use on: Bottles (Red wine/rose/white wine), Bussiness cards, vehicle signage, business signage, etc
P.S.:
If you have a design that is not outside the box we are still interested in seeing it.
Label is for a burgundy style bottle with a label height of 3.5 - 4" and a width of 3.5-4"
any label <= 4"x4" and >=3.5"x3.5" will be acceptable:
HOWEVER Width should be greater than or equal to height due to the bottle format
Target Market(s)
Wine enthusiasts with adequate discretionary budgets to afford $100 bottles of wine.
Industry/Entity Type
Wine / Winery
Requirements
Must have
- A sense of luxury, a feel of exclusivity, and a theme consistent with our product and brand name
Nice to have
- Tree line, wood grain or other wood themes. Serif fonts
Should not have
- anything cheesy, off topic, hard to read script fonts or anything that makes the label hard to read from a few feet away or too busy

```html
<!DOCTYPE html>
<html lang="en">
<head>
<meta charset="utf-8">
<title>Quailbrook Vineyards – Rosé Label</title>
<link rel="stylesheet" href="https://fonts.googleapis.com/css2?family=Abril+Fatface&family=Playfair+Display:ital,wght@0,400;1,400;1,700&family=Montserrat:wght@700&display=swap">
<style>
  :root {
    --paper: #fbf7ea;
    --cream: #f7f2e2;
    --gold: #e1b22a;
    --gold-deep: #c99a17;
    --forest: #0d4a2f;
    --wine: #8c1a1f;
    --ink: #111;
  }
  * { box-sizing: border-box; margin: 0; padding: 0; }
  html, body { width: 1200px; height: 673px; overflow: hidden; background: #fff; }
  .canvas { position: relative; width: 1200px; height: 673px; }
  .spec {
    position: absolute; top: 44px; left: 0; width: 100%;
    text-align: center; font: 700 18px/1 "Montserrat", sans-serif;
    letter-spacing: 2px; color: var(--ink);
  }
  .label {
    position: absolute; left: 322px; top: 80px; width: 555px; height: 536px;
    background: var(--paper);
  }
  .frame { position: absolute; inset: 0; }
  .treeline {
    position: absolute; left: 32px; top: 6px; width: 498px; height: 78px;
    background: linear-gradient(180deg, #1a6440 0%, var(--forest) 100%);
    clip-path: polygon(0 60%, 8% 10%, 16% 55%, 24% 20%, 32% 50%, 40% 30%, 48% 55%, 56% 15%, 64% 45%, 72% 0, 80% 40%, 88% 20%, 96% 50%, 100% 70%, 100% 100%, 0 100%);
  }
  .brand {
    position: absolute; left: 0; width: 100%; text-align: center;
    font-family: "Abril Fatface", serif; color: var(--forest);
  }
  .brand-name { top: 106px; font-size: 50px; line-height: 1; letter-spacing: 1px; }
  .brand-sub { top: 158px; font-size: 33px; line-height: 1; letter-spacing: 1px; }
  .tagline {
    position: absolute; left: 0; top: 201px; width: 100%; text-align: center;
    font: italic 400 11.5px/1 "Playfair Display", serif; letter-spacing: 1.3px;
    color: var(--gold); text-transform: uppercase;
  }
  .rose-mark {
    position: absolute; left: 246px; top: 243px; width: 64px; height: 64px;
    border-radius: 50%; background: var(--gold-deep);
  }
  .varietal {
    position: absolute; left: 192px; width: 172px; text-align: center; color: var(--gold);
  }
  .varietal-name { top: 312px; font: 400 48px/1 "Playfair Display", serif; }
  .vintage { top: 362px; font: 400 22px/1 "Abril Fatface", serif; }
  .notes {
    position: absolute; left: 66px; top: 277px; width: 106px; text-align: center;
    font: italic 400 11.5px/13.5px "Playfair Display", serif; letter-spacing: 1.2px;
    color: var(--gold); text-transform: uppercase;
  }
  .reserve {
    position: absolute; left: 386px; top: 281px; width: 104px; text-align: center;
    font: 400 17px/20.5px "Abril Fatface", serif; letter-spacing: .5px; color: var(--gold);
  }
  .producer {
    position: absolute; left: 0; top: 442px; width: 100%; text-align: center;
    font: 400 11px/13.5px "Abril Fatface", serif; letter-spacing: 2px; color: var(--gold);
  }
  .legal {
    position: absolute; left: 0; top: 480px; width: 100%; text-align: center;
    font: 400 14px/1 "Abril Fatface", serif; letter-spacing: 2.6px; color: var(--forest);
  }
  .legal .divider { display: inline-block; width: 1.5px; height: 17px; background: var(--forest); vertical-align: -3px; margin: 0 6px; }
</style>
</head>
<body>
<div class="canvas">
  <p class="spec">W4” X H3,85”</p>

  <section class="label" aria-label="Quailbrook Vineyards Rosé 2024 wine label">
    <svg class="frame" width="555" height="536" viewBox="0 0 555 536" aria-hidden="true">
      <!-- outer double border -->
      <rect x="10" y="10" width="535" height="516" fill="none" stroke="var(--gold)" stroke-width="3"/>
      <rect x="17" y="17" width="521" height="502" fill="none" stroke="var(--gold)" stroke-width="1.2"/>
      <rect x="24" y="24" width="507" height="488" fill="none" stroke="var(--gold)" stroke-width="1"/>
      <!-- title panel with notched corners -->
      <path d="M28 84 H527 L540 97 V218 L527 231 H28 L15 218 V97 Z" fill="var(--cream)" stroke="var(--gold)" stroke-width="3"/>
      <path d="M36 91 H519 L532 104 V211 L519 224 H36 L23 211 V104 Z" fill="none" stroke="var(--gold)" stroke-width="1"/>
      <!-- rules beside panels -->
      <line x1="71" y1="268" x2="166" y2="268" stroke="var(--gold)" stroke-width="1.5"/>
      <line x1="71" y1="373" x2="166" y2="373" stroke="var(--gold)" stroke-width="1.5"/>
      <line x1="390" y1="268" x2="486" y2="268" stroke="var(--gold)" stroke-width="1.5"/>
      <line x1="390" y1="373" x2="486" y2="373" stroke="var(--gold)" stroke-width="1.5"/>
      <!-- varietal banner -->
      <path d="M192 233 H364 V433 L278 410 L192 433 Z" fill="var(--gold)"/>
      <path d="M192 233 H364 V421 L278 398 L192 421 Z" fill="var(--wine)"/>
    </svg>

    <div class="treeline" role="img" aria-label="Evergreen tree line illustration in forest green with gold edges"></div>

    <h1 class="brand brand-name">QUAILBROOK</h1>
    <p class="brand brand-sub">VINEYARDS</p>
    <p class="tagline">“Handcrafted artisan wines from the Pacific Northwest”</p>

    <div class="rose-mark" role="img" aria-label="Gold line-drawn rose emblem"></div>
    <p class="varietal varietal-name">ROSÉ</p>
    <p class="varietal vintage">2024</p>

    <p class="notes">A refreshing, dry rosé with notes of wild strawberries, citrus, and a crisp, clean finish.</p>

    <p class="reserve">LIMITED<br>RESERVE<br>BATCH<br>NO. 12</p>

    <p class="producer">ESTATE GROWN ROSÉ WINE PRODUCED AND BOTTLED BY<br>QUAILBROOK VINEYARDS, OREGON, USA</p>
    <p class="legal">ALCOHOL 13.5% BY VOLUME<span class="divider"></span>750 ML</p>
  </section>
</div>
</body>
</html>
```